Website for Torvel Capital - investment banking firm

We have a corporate identity (thanks to Ravinka/31842) and want to extend that into a website design.  See the attached zipped files.
We have software folks in-house to do the coding.
See the attached Project Brief & Notes for more details.  Don't worry about the actual text - lorem ipsum will be fine.
The server will be Apache.
Thank you!
Desmond

Industry/Entity Type
Investment

```html
<!DOCTYPE html>
<html lang="en">
<head>
<meta charset="utf-8">
<title>Torvel Capital</title>
<link href="https://fonts.googleapis.com/css2?family=Raleway:wght@300;400;600;800&family=Open+Sans:wght@400;600&display=swap" rel="stylesheet">
<style>
:root{
  --blue-dark:#1b5d80;
  --blue:#2a82ab;
  --blue-light:#3e9cc3;
  --band:#79a6c4;
  --btn-teal:#114f6d;
  --btn-dark:#1c3140;
  --orange:#e8662c;
  --grey-text:#666;
  --grey-light:#f0f0f0;
  --ink:#222;
  --footer:#252525;
  --white:#fff;
}
*{margin:0;padding:0;box-sizing:border-box}
html,body{width:691px;height:1200px;overflow:hidden;background:var(--white)}
body{position:relative;font-family:'Open Sans',sans-serif;color:var(--ink)}
.abs{position:absolute}

/* hero */
.hero{left:0;top:0;width:691px;height:350px;background:linear-gradient(180deg,var(--blue-dark) 0%,var(--blue) 55%,var(--blue-light) 100%)}
.brand{left:42px;top:20px;display:flex;align-items:center;gap:10px;color:var(--white);font-family:'Raleway',sans-serif;font-weight:600;font-size:21px;letter-spacing:.5px}
.brand-mark{width:38px;height:38px;border-radius:50%;border:3px solid var(--white)}
.search{left:527px;top:22px;width:122px;height:17px;border-radius:9px;background:rgba(10,40,60,.6);color:#9bb;font-size:7px;padding:4px 0 0 18px}
.search svg{position:absolute;left:6px;top:5px}
.nav{top:56px;left:285px;display:flex;font-size:7.5px;color:var(--white);white-space:nowrap}
.nav span{padding:0 8px;height:17px;line-height:17px;text-transform:uppercase}
.nav .active{background:var(--white);color:var(--ink)}
.hero-title{left:42px;top:143px;font-family:'Raleway',sans-serif;font-weight:300;font-size:22px;line-height:23px;color:var(--white);white-space:nowrap}
.hero-title b{font-weight:800}
.hero-intro{left:43px;top:202px;width:310px;font-size:9.5px;line-height:14px;color:#e6f2f8}
.btn{display:flex;align-items:center;justify-content:center;color:var(--white);font-family:'Raleway',sans-serif;white-space:nowrap}
.hero-btn{top:246px;height:29px;width:123px;font-size:12px}
.band-btn{top:865px;height:24px;width:99px;font-size:10px}
.btn-teal{background:var(--btn-teal)}
.btn-dark{background:var(--btn-dark)}
.globe{left:425px;top:92px;width:190px;height:248px;border-radius:95px 95px 20px 20px;background:radial-gradient(circle at 45% 35%,#b9c4a8 0%,#7d8c76 55%,#2a6e8f 100%)}

/* tabs */
.tabs{left:0;top:350px;width:691px;height:71px;background:var(--grey-light);display:flex;padding-left:43px}
.tab{width:101px;border-left:1px solid #ddd;display:flex;align-items:center;justify-content:center;text-align:center;font-family:'Raleway',sans-serif;font-weight:600;font-size:8.5px;line-height:11px;color:#555}
.tab:last-child{border-right:1px solid #ddd}
.tab.active{color:var(--orange)}

/* welcome */
.welcome-title{left:43px;top:458px;font-family:'Raleway',sans-serif;font-weight:400;font-size:17px}
.about{left:44px;top:503px;width:232px;font-family:'Raleway',sans-serif;font-size:9.6px;line-height:15.2px;color:var(--grey-text)}
.benefits{left:285px;top:506px;font-family:'Raleway',sans-serif;font-size:8px;color:#888}
.benefits h3{font-size:8px;font-weight:600;color:#555;margin-bottom:6px}
.benefits li{list-style:none;line-height:12.3px;white-space:nowrap}
.benefits li:before{content:"›";margin-right:6px}
.figure-benefits{left:410px;top:445px;width:240px;height:198px;border-radius:6px;background:radial-gradient(circle at 45% 55%,#f4c2ad 0%,#eaf2fb 55%,#fff 100%)}

/* band */
.band{left:0;top:700px;width:691px;height:231px;background:var(--band)}
.band-title{left:42px;top:720px;font-family:'Raleway',sans-serif;font-weight:300;font-size:20px;line-height:22px;color:var(--white)}
.band-intro{left:42px;top:782px;width:265px;font-size:9.3px;line-height:13.6px;color:#eef5fa}
.map{left:320px;top:688px;width:303px;height:155px;background:linear-gradient(135deg,#d8e3c8 0%,#e9ecd9 50%,#a9c6e6 100%);transform:skewX(-4deg)}

/* features */
.features-title{left:45px;top:947px;width:400px;font-family:'Raleway',sans-serif;font-weight:400;font-size:12.5px;line-height:17px}
.feature{top:991px;width:130px;text-align:center}
.feature .icon{width:69px;height:69px;border-radius:50%;background:#4a4a4a;margin:0 auto;display:flex;align-items:center;justify-content:center}
.feature h4{margin-top:12px;font-family:'Raleway',sans-serif;font-weight:400;font-size:10px;color:#444}
.feature p{margin-top:6px;font-size:6.3px;line-height:8px;color:#888}
.feature .more{margin:7px auto 0;width:60px;height:15px;background:var(--btn-teal);color:var(--white);font-size:7px;line-height:15px;border-radius:2px}

/* newsletter */
.newsletter{left:495px;top:947px;width:152px}
.newsletter h2{font-family:'Raleway',sans-serif;font-weight:400;font-size:12.5px;padding-bottom:14px;border-bottom:1px solid #e4e4e4}
.newsletter p{margin-top:13px;font-size:7.2px;line-height:11px;color:#555}
.newsletter small{display:block;margin-top:4px;font-size:5.5px;color:#aaa}
.field{margin-top:11px;height:20px;background:#ececec;border:1px solid #ddd;font-size:7px;color:#999;padding:5px 6px}
.field+.field{margin-top:13px}
.subscribe{margin-top:12px;width:72px;height:20px;background:var(--blue-dark);color:var(--white);font-size:9px;line-height:20px;text-align:center}

/* footer */
.footer{left:0;top:1168px;width:691px;height:32px;background:var(--footer);color:#ddd;font-size:7.5px;display:flex;align-items:center;justify-content:space-between;padding:0 42px}
.footer nav span{margin-left:8px}
</style>
</head>
<body>

<header class="abs hero"></header>
<div class="abs brand"><span class="brand-mark"></span>Torvel Capital</div>
<div class="abs search">
  <svg width="7" height="7" viewBox="0 0 10 10"><circle cx="4" cy="4" r="3" fill="none" stroke="#9bb" stroke-width="1.5"/><line x1="6.3" y1="6.3" x2="9" y2="9" stroke="#9bb" stroke-width="1.5"/></svg>Search...
</div>
<nav class="abs nav">
  <span class="active">Home</span><span>About</span><span>Services</span><span>Current Engagements</span><span>Completed Transactions</span>
</nav>
<h1 class="abs hero-title">Torvel Capital, LLC <b>Investment</b><br>Banking |Mergers &amp; Acquisitions</h1>
<p class="abs hero-intro">Sed ut perspiciatis unde omnis iste natus error sit voluptatem accu-santium doloremque laudantium, totam rem aperiam, eaque ipsa</p>
<div class="abs btn btn-teal hero-btn" style="left:42px">See the features</div>
<div class="abs btn btn-dark hero-btn" style="left:176px">Get a Free Demo</div>
<div class="abs globe" role="img" aria-label="Globe made of banknote bundles on a brass stand"></div>

<div class="abs tabs">
  <div class="tab active">Program<br>Management</div>
  <div class="tab">Integrated<br>Logistics Support</div>
  <div class="tab">Configuration<br>Management</div>
  <div class="tab">Engineering<br>&amp; Support</div>
  <div class="tab">Financial<br>Management</div>
  <div class="tab">Information<br>Technology</div>
</div>

<h2 class="abs welcome-title">Welcome to Torvel Capital Invesment</h2>
<p class="abs about">Norvane's aim is to maintain a dynamic benefits package, which will more than meet the needs of the company's employees. As such, Norvane's benefits are under continuous review and may be modified at any time, without notice. A complete copy of each Plan description is available from our Human Resources.</p>
<div class="abs benefits">
  <h3>Benefits at a Glance:</h3>
  <ul>
    <li>3 Weeks Leave</li><li>8 Holidays</li><li>Health, Dental, &amp; Life Insuranc</li><li>Tuition Assistance</li><li>Flexible Spending Account</li><li>401(k)</li>
  </ul>
</div>
<div class="abs figure-benefits" role="img" aria-label="Illustration of an investor holding a money bag with arrows pointing to home, oil, business, growth and documents"></div>

<section class="abs band"></section>
<div class="abs map" role="img" aria-label="Folded map of the United States with office location pins"></div>
<h2 class="abs band-title">Global Investment Banking<br>Services</h2>
<p class="abs band-intro">Sed ut perspiciatis unde omnis iste natus error sit voluptatem accusantium doloremque laudantium, totam rem aperiam, eaque ipsa quae ab illo inventore veritatis et quasi architecto beatae vitae dicta sunt explicabo. Nemo enim ipsam voluptatem quia voluptas sit aspernatur aut odit aut</p>
<div class="abs btn btn-teal band-btn" style="left:40px">See the features</div>
<div class="abs btn btn-dark band-btn" style="left:148px">Get a Free Demo</div>

<h2 class="abs features-title">Positioning statement :Global, Professional, Trusted or Disciplined Effective</h2>
<div class="abs feature" style="left:43px">
  <div class="icon"><svg width="34" height="40" viewBox="0 0 34 40"><text x="17" y="34" text-anchor="middle" font-family="Arial,sans-serif" font-weight="700" font-size="40" fill="#fff">?</text></svg></div>
  <h4>Who we are</h4>
  <p>Lorem ipsum dolor sit amet elit, sed do eiusmod tempor incididunt</p>
  <div class="more">Read More</div>
</div>
<div class="abs feature" style="left:181px">
  <div class="icon"><svg width="34" height="30" viewBox="0 0 34 30"><g fill="#fff"><circle cx="12" cy="13" r="8"/><circle cx="24" cy="8" r="5"/><circle cx="25" cy="22" r="5"/></g><g fill="#4a4a4a"><circle cx="12" cy="13" r="3"/><circle cx="24" cy="8" r="2"/><circle cx="25" cy="22" r="2"/></g></svg></div>
  <h4>Our services</h4>
  <p>Lorem ipsum dolor sit amet elit, sed do eiusmod tempor incididunt</p>
  <div class="more">Read More</div>
</div>
<div class="abs feature" style="left:309px">
  <div class="icon"><svg width="28" height="28" viewBox="0 0 28 28"><g fill="#fff"><rect x="0" y="0" width="12" height="12" rx="2"/><rect x="16" y="0" width="12" height="12" rx="2"/><rect x="0" y="16" width="12" height="12" rx="2"/><rect x="16" y="16" width="12" height="12" rx="2"/></g></svg></div>
  <h4>Who we are</h4>
  <p>Lorem ipsum dolor sit amet elit, sed do eiusmod tempor incididunt</p>
  <div class="more">Read More</div>
</div>

<aside class="abs newsletter">
  <h2>Subscribe to newsletter</h2>
  <p>Subscribe to our monthly newsletter to be updated with our new offers.</p>
  <small>Your email address is safe and we also hate Spam</small>
  <div class="field">Name</div>
  <div class="field">Email</div>
  <div class="subscribe">Subscribe</div>
</aside>

<footer class="abs footer">
  <span>© Copyright 2014. All rights reserved.</span>
  <nav><span>Home</span><span>About</span><span>Service</span><span>Current Engagements</span><span>Completed Transactions</span></nav>
</footer>

</body>
</html>
```